Pendleford Real Estate Partners Looking For FUNNY, SEXY & KICK ASS Billboards!

We are launching our billboard campaign Jan 2021 and will need 8 billboards. We have some hilarious ideas but need a professional to help us! We are a male and female based real estate partnership selling commercial and residential properties in New Brunswick Canada. We have a lot of ideas but need direction.

Target Market(s)

Sellers and Buyers of Real Estate

Industry/Entity Type

Real Estate Agent

Font styles to use
Serif

Colors

Designer to choose only greyscale colors for use in the design.

Requirements
Must have
• Funny, sassy and eye-catching. We like to have fun and want out billboards to make people smile.
Nice to have
• Movies references having to do with real estate (we have ideas) WE would like the project to be cohesive over the 8 billboards.
Should not have
• Too much colour or too generic. We have our brand colours we would like to stick with. Black, white and red accent.

```html
<!DOCTYPE html>
<html lang="en">
<head>
<meta charset="UTF-8">
<title>Pendleford Real Estate Partners – Billboard</title>
<link rel="stylesheet" href="https://fonts.googleapis.com/css2?family=Cinzel:wght@700&family=Oswald:wght@600&family=Open+Sans:wght@600;700&family=Gochi+Hand&display=swap">
<style>
  :root {
    --brand-red: #e31e25;
    --ink: #111111;
    --paper: #ffffff;
    --bubble-light: #f4f4f4;
    --bubble-dark: #c4c4c4;
    --photo-light: #3a3a3a;
    --photo-dark: #0e0e0e;
  }
  * { margin: 0; padding: 0; box-sizing: border-box; }
  html, body { width: 1200px; height: 600px; overflow: hidden; background: var(--paper); }
  .billboard {
    position: relative;
    width: 1200px;
    height: 600px;
    background: var(--paper);
    overflow: hidden;
  }
  .footer-band {
    position: absolute;
    left: 0; top: 493px;
    width: 1200px; height: 107px;
    background: var(--brand-red);
  }
  .team-photo {
    position: absolute;
    left: 160px; top: 135px;
    width: 360px; height: 465px;
    background: linear-gradient(180deg, var(--photo-light) 0%, var(--photo-dark) 70%);
    border-radius: 110px 110px 0 0;
  }
  .speech-bubbles {
    position: absolute;
    left: 0; top: 0;
    width: 600px; height: 220px;
  }
  .bubble-line {
    position: absolute;
    font-family: "Gochi Hand", cursive;
    color: var(--brand-red);
    line-height: 1;
    white-space: nowrap;
  }
  .bubble-line--question {
    left: 66px; top: 50px;
    font-size: 31px;
    text-align: center;
    transform: rotate(-9deg);
    line-height: 1.05;
  }
  .bubble-line--answer {
    left: 436px; top: 97px;
    font-size: 25px;
  }
  .brokerage {
    position: absolute;
    left: 17px; top: 438px;
    display: flex;
    align-items: center;
    gap: 5px;
    font-family: "Open Sans", sans-serif;
    font-weight: 700;
    font-size: 12px;
    color: var(--ink);
    white-space: nowrap;
  }
  .brokerage-mark {
    width: 14px; height: 14px;
    background: var(--brand-red);
  }
  .wordmark {
    position: absolute;
    left: 529px; top: 216px;
    width: 654px;
    font-family: "Cinzel", serif;
    font-weight: 700;
    font-size: 92px;
    line-height: 1;
    color: var(--ink);
    text-align: center;
    letter-spacing: -1px;
    white-space: nowrap;
  }
  .tagline {
    position: absolute;
    left: 557px; top: 312px;
    width: 600px;
    font-family: "Oswald", sans-serif;
    font-weight: 600;
    font-size: 28px;
    line-height: 1;
    color: var(--ink);
    display: flex;
    justify-content: space-between;
  }
  .contacts {
    position: absolute;
    left: 600px; top: 398px;
    width: 522px;
    font-family: "Open Sans", sans-serif;
    font-weight: 600;
    font-size: 31px;
    color: var(--ink);
    text-align: center;
    white-space: nowrap;
  }
  .contacts .phone { font-weight: 700; }
  .contacts .divider {
    display: inline-block;
    width: 4px; height: 34px;
    background: var(--brand-red);
    vertical-align: -6px;
    margin: 0 8px;
  }
  .website {
    position: absolute;
    left: 540px; top: 514px;
    width: 636px;
    font-family: "Open Sans", sans-serif;
    font-weight: 700;
    font-size: 45px;
    color: var(--paper);
    text-align: center;
    line-height: 1.2;
    white-space: nowrap;
  }
</style>
</head>
<body>
<main class="billboard">
  <div class="footer-band"></div>

  <div class="team-photo" role="img" aria-label="Photo of the two partners in dark business attire, standing side by side"></div>

  <svg class="speech-bubbles" viewBox="0 0 600 220" aria-hidden="true">
    <defs>
      <radialGradient id="bubbleShade" cx="50%" cy="40%" r="65%">
        <stop offset="0%" stop-color="var(--bubble-light)"/>
        <stop offset="100%" stop-color="var(--bubble-dark)"/>
      </radialGradient>
    </defs>
    <path d="M62 72 C48 45 90 30 118 42 C135 18 190 14 210 30 C235 12 285 22 282 55 C300 68 292 110 262 118 C255 140 222 148 200 138 C190 148 175 150 165 146 L196 191 L142 142 C110 150 75 135 78 115 C42 112 36 82 62 72 Z" fill="url(#bubbleShade)"/>
    <path d="M440 82 C428 64 450 52 465 60 C472 44 505 42 516 58 C540 52 560 70 552 88 C572 98 568 130 545 134 C535 150 505 152 495 142 L462 203 L478 142 C455 144 428 130 434 112 C418 106 422 84 440 82 Z" fill="url(#bubbleShade)"/>
  </svg>
  <p class="bubble-line bubble-line--question">Hey Girl!<br>What's your sign?</p>
  <p class="bubble-line bubble-line--answer">Here's mine</p>

  <div class="brokerage">
    <span class="brokerage-mark"></span>
    <span class="brokerage-name">NORTHGATE REALTY</span>
  </div>

  <h1 class="wordmark">PENDLEFORD</h1>
  <p class="tagline">
    <span>R</span><span>E</span><span>A</span><span>L</span><span>&nbsp;</span>
    <span>E</span><span>S</span><span>T</span><span>A</span><span>T</span><span>E</span><span>&nbsp;</span>
    <span>P</span><span>A</span><span>R</span><span>T</span><span>N</span><span>E</span><span>R</span><span>S</span>
  </p>

  <p class="contacts">
    Dana <span class="phone">555-0142</span><span class="divider"></span>Marcus <span class="phone">555-0187</span>
  </p>

  <p class="website">www.pendlefordhomes.ca</p>
</main>
</body>
</html>
```